New Business Card for Web Design/Internet Marketing Company

Looking for a great looking new business card. We are a 10 year old web design, internet marketing and website management company that works mostly with small businesses.

Our new card needs to better match the colors and style of our website, be bold, extremely usable and slightly edgy.

Target Market(s)

Small/Medium businesses that have websites

Industry/Entity Type

Internet

Requirements
Must have
• Front and back design, full color, rounded corners please

Must use the colors/style of our website (JPG provided)

INFO FOR CARDS (as readable as possible please)
Mark Lenner
President/CEO
mark@trelvanmedia.example
Phone: 520-381-7459
Toll Free: 866-381-7459
Address: 4315 W. Calloway Ave. Ste. 140, Tucson, AZ 85792

THINGS I WANT TO PROMOTE (if there is room):
1. Our Website - www.trelvanmedia.example

2. Social Media
Twitter: @trelvanmedia
Facebook: www.facebook.com/trelvanmedia

3. Our Services
Web Design
Internet Marketing
Website Management

```html
<!DOCTYPE html>
<html lang="en">
<head>
<meta charset="utf-8">
<title>Trelvan Media – Business Card</title>
<link href="https://fonts.googleapis.com/css2?family=Lato:wght@400;700&display=swap" rel="stylesheet">
<style>
  :root {
    --stage: #eceae6;
    --blue-deep: #1690cf;
    --blue-light: #8fd4f0;
    --panel: #f7f8f8;
    --navy: #1d3b6e;
    --brand-blue: #1a78b8;
    --orange: #e47f12;
    --ink: #2b2b2b;
    --icon: #c98a3a;
  }
  * { box-sizing: border-box; margin: 0; padding: 0; }
  html, body { width: 1200px; height: 720px; overflow: hidden; }
  body {
    background: var(--stage);
    font-family: "Lato", sans-serif;
    position: relative;
  }
  .card {
    position: absolute;
    top: 205px;
    width: 540px;
    height: 309px;
    border-radius: 14px;
    overflow: hidden;
    background: linear-gradient(180deg, var(--blue-light) 0%, var(--blue-deep) 100%);
    box-shadow: 0 6px 18px rgba(0,0,0,.15);
  }
  .card--front { left: 30px; }
  .card--back { left: 630px; }

  /* front */
  .front-panel {
    position: absolute;
    left: 52px; right: 0;
    top: 62px; bottom: 52px;
    background: var(--panel);
  }
  .brand {
    display: flex; align-items: center; gap: 8px;
    color: var(--brand-blue);
    font-weight: 700;
  }
  .brand__dot {
    border-radius: 50%;
    background: var(--orange);
    flex: none;
  }
  .front-panel .brand { position: absolute; left: 18px; top: 18px; font-size: 24px; }
  .front-panel .brand__dot { width: 22px; height: 22px; }
  .person {
    position: absolute; left: 18px; top: 78px;
    font-size: 17px; color: var(--ink);
  }
  .person__role { font-size: 14px; letter-spacing: .04em; }
  .contact-list {
    position: absolute; left: 18px; bottom: 14px;
    list-style: none; font-size: 12.5px; color: var(--ink); line-height: 1.35;
  }
  .contact-list li { display: flex; align-items: center; gap: 10px; }
  .contact-list svg { width: 12px; height: 12px; fill: none; stroke: var(--icon); stroke-width: 1.6; }
  .social {
    position: absolute; right: 22px; top: 12px;
    list-style: none; font-size: 12.5px; color: var(--ink); line-height: 1.9;
  }
  .social li { display: flex; align-items: center; gap: 9px; }
  .social__mark { width: 14px; height: 14px; border-radius: 2px; background: var(--brand-blue); }
  .address {
    position: absolute; right: 22px; bottom: 16px;
    font-size: 11.5px; color: var(--ink); line-height: 1.3;
  }
  .address__web { color: var(--orange); font-weight: 700; }

  /* back */
  .back-logo-box {
    position: absolute; left: 60px; right: 60px; top: 36px; height: 112px;
    background: var(--panel);
    display: flex; align-items: center; justify-content: center;
  }
  .back-logo-box .brand { font-size: 36px; gap: 12px; }
  .back-logo-box .brand__dot { width: 32px; height: 32px; }
  .services-band {
    position: absolute; left: 0; right: 0; top: 160px; height: 78px;
    background: var(--panel);
    display: flex; align-items: center; justify-content: center;
    color: var(--navy); font-size: 15px; gap: 10px;
  }
  .services-band .sep { color: #8aa0bd; }
</style>
</head>
<body>

  <section class="card card--front" aria-label="Business card front">
    <div class="front-panel">
      <div class="brand"><span class="brand__dot"></span><span>Trelvan Media</span></div>

      <p class="person">Mark Lenner <span class="person__role">| PRESIDENT / CEO</span></p>

      <ul class="contact-list">
        <li>
          <svg viewBox="0 0 12 12"><rect x="2" y="1" width="8" height="10" rx="1.5"/><line x1="4.5" y1="9" x2="7.5" y2="9"/></svg>
          520-381-7459
        </li>
        <li>
          <svg viewBox="0 0 12 12"><path d="M2 4 a4 4 0 0 1 8 0 v1 h-2 v-1 a2 2 0 0 0-4 0 v1 h-2z"/><rect x="2" y="6" width="8" height="5" rx="1"/></svg>
          866-381-7459 free
        </li>
        <li>
          <svg viewBox="0 0 12 12"><rect x="1" y="2.5" width="10" height="7"/><polyline points="1,2.5 6,7 11,2.5"/></svg>
          mark@trelvanmedia.example
        </li>
      </ul>

      <ul class="social">
        <li><span class="social__mark"></span>@trelvanmedia</li>
        <li><span class="social__mark"></span>/trelvanmedia</li>
      </ul>

      <p class="address">
        4315 W. Calloway Ave. Ste. 140,<br>
        Tucson, AZ 85792<br>
        <span class="address__web">www.trelvanmedia.example</span>
      </p>
    </div>
  </section>

  <section class="card card--back" aria-label="Business card back">
    <div class="back-logo-box">
      <div class="brand"><span class="brand__dot"></span><span>Trelvan Media</span></div>
    </div>
    <div class="services-band">
      <span>Web Design</span><span class="sep">|</span>
      <span>Internet Marketing</span><span class="sep">|</span>
      <span>Website Management</span>
    </div>
  </section>

</body>
</html>
```